Modern Attractive Letterhead for Veterinary House Call Business.

A letterhead which can be printed on A4, A5 and A6 paper sizes.
To have: ( our files to be uploaded)
1. Logo with Text
2. telephone
3. email
4. website
5. Address

Target Market(s)

60-85year mainly women pet owners. Also market include families, young professionals, busy people who have dogs and cats

Industry/Entity Type

Business

Requirements
Must have
• 1. Logo with Text ( provided)
• 2. telephone
• 3. email
• 4. website
• 5. Address
Nice to have
• Needs to be modern, preferably warm and caring in nature( if possible )
Should not have
• difficulty in printing A5 and A6

```html
<!DOCTYPE html>
<html lang="en">
<head>
<meta charset="utf-8">
<title>Wellnest Vet Care – Letterhead</title>
<link rel="stylesheet" href="https://fonts.googleapis.com/css2?family=Cinzel:wght@400;600&display=swap">
<style>
  :root {
    --backdrop: #e9e9e7;
    --paper: #ffffff;
    --brand-blue: #1d4fa3;
    --band-deep: #1b3f9e;
    --band-light: #3fb3ea;
    --leaf-green: #5bb53a;
    --ink: #1a1a1a;
    --rule: #6d6d6d;
    --icon-blue: #3a8fd8;
  }
  * { box-sizing: border-box; margin: 0; padding: 0; }
  html, body {
    width: 982px;
    height: 1200px;
    overflow: hidden;
    background: var(--backdrop);
  }
  .letterhead {
    position: absolute;
    left: 51px;
    top: 30px;
    width: 880px;
    height: 1140px;
    background: var(--paper);
    box-shadow: 0 2px 10px rgba(0,0,0,0.12);
    font-family: "Cinzel", "Times New Roman", serif;
  }
  .brand {
    position: absolute;
    left: 28px;
    top: 54px;
    display: flex;
    align-items: center;
    gap: 16px;
  }
  .brand-square {
    width: 58px;
    height: 58px;
    background: var(--brand-blue);
  }
  .brand-name {
    font-size: 40px;
    font-weight: 600;
    letter-spacing: 1px;
    color: var(--brand-blue);
    line-height: 1;
  }
  .postal {
    position: absolute;
    left: 588px;
    top: 52px;
    padding-left: 10px;
    border-left: 1px solid var(--rule);
    height: 56px;
    display: flex;
    gap: 8px;
  }
  .postal-icon { width: 17px; height: 16px; margin-top: 6px; flex: none; }
  .postal-lines {
    font-size: 17px;
    line-height: 21px;
    color: var(--ink);
    letter-spacing: 0.5px;
    padding-top: 2px;
  }
  .footer-rule {
    position: absolute;
    left: 0;
    width: 100%;
    height: 2px;
    background: var(--leaf-green);
  }
  .footer-rule.top { top: 1016px; }
  .footer-rule.bottom { top: 1055px; }
  .contact-band {
    position: absolute;
    left: 0;
    top: 1022px;
    width: 100%;
    height: 28px;
    background: linear-gradient(90deg, var(--band-deep) 0%, var(--band-deep) 25%, var(--band-light) 50%, var(--band-deep) 75%, var(--band-deep) 100%);
    display: flex;
    align-items: center;
    padding-left: 44px;
    gap: 30px;
    color: #ffffff;
    font-size: 16px;
    letter-spacing: 0.4px;
  }
  .contact-item { display: flex; align-items: center; gap: 7px; white-space: nowrap; }
  .contact-item svg { width: 15px; height: 15px; flex: none; }
</style>
</head>
<body>
  <main class="letterhead">
    <header class="brand">
      <span class="brand-square" aria-hidden="true"></span>
      <span class="brand-name">Wellnest Vet Care</span>
    </header>

    <address class="postal" style="font-style: normal;">
      <svg class="postal-icon" viewBox="0 0 17 16" aria-hidden="true">
        <path d="M8.5 1 L16 8 H13.5 V15 H10 V10.5 H7 V15 H3.5 V8 H1 Z" fill="var(--icon-blue)"/>
      </svg>
      <div class="postal-lines">
        <div>Po Box 4410</div>
        <div>Fernbrook Qld 4070</div>
      </div>
    </address>

    <div class="footer-rule top"></div>
    <footer class="contact-band">
      <span class="contact-item">
        <svg viewBox="0 0 16 16" aria-hidden="true">
          <circle cx="8" cy="8" r="7" fill="none" stroke="#fff" stroke-width="1.3"/>
          <path d="M5.5 4.5 L7 4.3 L7.6 6.3 L6.8 7 C7.3 8.2 8 9 9.1 9.4 L9.8 8.6 L11.7 9.2 L11.5 10.8 C8 11.2 5 8 5.5 4.5 Z" fill="#fff"/>
        </svg>
        0455218930
      </span>
      <span class="contact-item">
        <svg viewBox="0 0 16 16" aria-hidden="true">
          <rect x="1" y="3.5" width="14" height="9" fill="#fff"/>
          <path d="M1 3.5 L8 9 L15 3.5" fill="none" stroke="var(--band-deep)" stroke-width="1.2"/>
        </svg>
        Info@wellnestvetcare.com.au
      </span>
      <span class="contact-item">
        <svg viewBox="0 0 16 16" aria-hidden="true">
          <g fill="none" stroke="#fff" stroke-width="1.1">
            <circle cx="8" cy="8" r="6.5"/>
            <ellipse cx="8" cy="8" rx="3" ry="6.5"/>
            <line x1="1.5" y1="8" x2="14.5" y2="8"/>
            <path d="M2.6 4.8 H13.4 M2.6 11.2 H13.4"/>
          </g>
        </svg>
        Www.wellnestvetcare.com.au
      </span>
    </footer>
    <div class="footer-rule bottom"></div>
  </main>
</body>
</html>
```